Blood Testing Health App

We are looking for a graphics designer to create a web app for us so that we may insert it into a health management website system.
For branding purposes we are at www.Vantiqor.com and we are revamping our website... Example of new colors attached.
How we work...
We are a blood testing company based in the USA.
We offer a blood testing service nationwide in the USA.
We allow customers to order tests directly from us, visit a lab, have their blood drawn, or submit a urine sample, the lab tests it and they send the results back to our computer system and we share it with the customer.
The benefits of this are the customer does not need to go to the doctor and pay for the doctors visit to order these tests, which save them money. The tests are cheaper than going through the doctor. The customer simply uses us to get the test and the results and they can then take the results to their doctor... this process has saved them money. Others may be interested in regular check ups for blood work etc... and this allows them to do it with out needing a doctor, or if you have no insurance, this is a cheaper option too. We are quicker than a doctor, customers do not need appointments etc.
Hopefully you now have a better understanding as to what we do.
Here is the spec.
The app screen size is 750 px wide by 700 px high. ( A pdf is attached to show where the app is going to go, it is on page 3 of the pdf) The customer will have the ability to scroll… therefore the length of the page can be longer.
The app will consist of the following sections
Entry Page –
This will be the first page the user sees upon opening the app. This will be where they are directed from to the sections of the app discussed below. This needs to be branded for VantiQor with a modern look.
1 – Order Test (Giving them the ability to purchase a blood test within the app)
2 – VantiQor Dashboard (A dashboard that has everything they could need to use our service_
How it works Section on entry page – this will be a simple set of graphics showing how the service works. We already have the graphics for this, they do not need to be built again. They are attached to this brief
Basic structure of sections –
Order Test –
This page contains all tests, filed in categories – and Sub categories – Each test needs a link to an Information section – Price – Buy Now – Cart Process
VantiQor Dashboard –
A page of icons along the top of the app
- My Confirmation
- My Nearest Lab
- My Receipt
- My Orders
- My Account
- My Results
- My Inbox
- Contact Us
Sections in more detail -
Order A Test –
Show all categories/ sub categories – There are 23 categories, 14 sub categories, and within these categories are 300 tests - Here is the information for the categories etc - http://www.vantiqor.com/panels.aspx?PanelGroupID=4 Just in case it helps :)
We need to present this in a graphic format that is spacious, modern (brimlake, kivvo web appearance is the direction we are going for) We need it to be clear and not overwhelming to the customer.
Functionality idea…
Customer clicks category/ subcategory and tests appear.
Customer sees small 35 word description. For more information the test opens into a lightbox or expand the container which ever graphic designer believes to be most visually appealing
Buy Now must always be visible, along with price of the test
Buying process explained – Customer clicks buy now –
They are then taken to a Review Order screen ( This contains Order summary and choose payment method – insert payment details )
– Confirm payment –
Confirmation screen appears, thanking them.
They are then taken to the VantiQor Dashboard...
VantiQor Dashboard –
"My Confirmation" - Print Confirmation Order (PDF is in brief, we want this web based not a pdf download)
"My Nearest Lab Location" - This does not need to be designed because the web developer has this part under control, but we do need the icon in the dashboard
"My Receipt" - Print receipt - This does not exist in our system yet. So we need to create this from scratch - It will need to have - The test they are purchasing and the amount of the test - The customers name - The order ID - Must provide printer friendly option too
"My Orders" - This will have a list of orders - At the end of each order will be a status update of either "Test results" "Open order"
A graphic table format would be perfect. This will be linked to relevant results if they have been received. I have also attached a version of what the customer currently sees on our website. We know it is nasty ;) We are redesigning... but the information is there for this section to help design it with the right info. If the results are ready it will say in this list.
"Results Ready" will be a link to show those results once the customer has clicked the link, and the results will appear in the app, under the icons. There must be a printer friendly version too.
"My Results" Developer will sort this page out but we need the icon... It will be exactly like my orders but only show test results
"My Account" - This will be a place for them to update their personal information - Name, DOB, Address, Email Address
"My Inbox" - An inbox interface - Our way of contacting the customer for promotions we are running etc – We need a design of how this screen will appear. We also need the icon in the dashboard to have a notification on it if there are messages in the customers inbox. A little red 1, or circle with number of messages in the inbox.
"Customer Service" - This does not need to be designed because the web developer has this part under control, but we do need the icon in the dashboard
Icons appear along the top of app ( example - Mac icons/ iphone app icons) When the customer clicks an icon the content always appears below the icons
Here is more information for the icons and what should appear when each icon is clicked.
Screens to be designed –
Entry Page
Order A Test Page
Review Order Screen/Payment Screen - Show a lightbox that shows payment has been confirmed. Customer clicks close and are on the Confirmation Screen
VantiQor Dashboard - Screens mentioned in detail above
We can't wait to see your designs!
Please email any questions.
Hi all this is the first time we have used pixel harbor and understand the budget was too low for this project. We have now increased the budget to $2,000 and extended the deadline by another week
Hi all we are receiving some really great designs. I just added an example of the space that the web app will be going into... It is called "morvelapp.pdf"
Hi guys updated the brief. Hopefully this will help with the dashboard part of the design

```html
<!DOCTYPE html>
<html lang="en">
<head>
<meta charset="utf-8">
<title>VantiQor – My Account</title>
<link rel="stylesheet" href="https://fonts.googleapis.com/css2?family=Open+Sans:wght@400;600;700&display=swap">
<style>
  :root{
    --green:#84a41a;
    --green-light:#9bbd2a;
    --ink:#222222;
    --text:#444444;
    --muted:#8a8a8a;
    --field:#f2f2f2;
    --field-line:#dcdcdc;
    --band-top:#f2f2f2;
    --band-bottom:#dedede;
    --panel:#ebebeb;
    --tab:#e8e8e8;
    --active:#1a6fc2;
    --icon:#555a5c;
    --orange-top:#ff7d1f;
    --orange-bottom:#f04c00;
    --alert:#f03c12;
    --white:#ffffff;
  }
  *{box-sizing:border-box;margin:0;padding:0}
  html,body{width:1200px;height:1197px;overflow:hidden;background:var(--white)}
  body{position:relative;font-family:"Open Sans",Arial,sans-serif;color:var(--text)}

  .site-header{position:absolute;left:0;top:0;width:1200px;height:162px;background:var(--white)}
  .brand{position:absolute;left:42px;top:58px;display:flex;align-items:center;gap:16px}
  .brand-mark{width:30px;height:30px;background:var(--green)}
  .brand-name{font-size:58px;font-weight:600;color:var(--ink);letter-spacing:1px;line-height:1}

  .main-tab{position:absolute;top:46px;height:116px;width:198px;text-align:center;
    font-size:17px;text-transform:uppercase;letter-spacing:.3px}
  .main-tab svg{display:block;margin:22px auto 10px}
  .tab-order{left:541px;color:var(--muted)}
  .tab-dashboard{left:730px;background:var(--tab);border-radius:13px 13px 0 0;color:var(--green)}

  .social{position:absolute;top:101px;width:44px;height:44px;border-radius:50%;background:var(--green-light)}

  .icon-bar{position:absolute;left:0;top:162px;width:1200px;height:216px;
    background:linear-gradient(var(--band-top),var(--band-bottom))}
  .icon-bar::after{content:"";position:absolute;left:752px;bottom:0;border:16px solid transparent;
    border-bottom-color:var(--white);border-top:0}
  .dash-item{position:absolute;top:48px;width:170px;margin-left:-85px;text-align:center;
    font-size:21px;color:var(--text);line-height:1.05}
  .dash-item.is-active{color:var(--active);font-weight:700}
  .dash-icon{width:96px;height:96px;margin:0 auto 14px;border-radius:50%;position:relative;
    background:linear-gradient(#ffffff,#d2d2d2);box-shadow:0 3px 5px rgba(0,0,0,.25),inset 0 -2px 3px rgba(0,0,0,.08);
    display:flex;align-items:center;justify-content:center}
  .person-slot{width:58px;height:62px;border-radius:29px 29px 10px 10px}
  .badge{position:absolute;right:-12px;top:-8px;min-width:45px;height:29px;border-radius:6px;
    background:var(--alert);color:var(--white);font-size:18px;line-height:29px;text-align:center}

  .panel{position:absolute;left:27px;top:421px;width:1139px;height:720px;background:var(--panel);border-radius:13px}
  .card{position:absolute;left:18px;top:21px;width:1102px;height:673px;background:var(--white);border-radius:13px;overflow:hidden}
  .card-title{height:75px;background:var(--green);color:var(--white);font-size:32px;font-weight:400;
    padding-left:24px;line-height:78px;text-transform:uppercase}

  .field{position:absolute;height:62px;background:var(--field);border:1px solid var(--field-line);
    border-radius:16px;font-size:22px;color:var(--text);line-height:60px;padding-left:22px}
  .field.select{padding-left:20px}
  .field.select svg{position:absolute;right:22px;top:20px}

  .submit{position:absolute;left:38px;top:524px;width:319px;height:74px;border-radius:12px;
    background:linear-gradient(var(--orange-top),var(--orange-bottom));border:2px solid #ff9a55;
    box-shadow:0 2px 3px rgba(0,0,0,.2);color:var(--white);font-size:25px;font-weight:700;
    display:flex;align-items:center;padding-left:26px;gap:20px}
  .submit-icon{width:36px;height:36px;border-radius:50%;background:#c8400a;display:flex;align-items:center;justify-content:center}
</style>
</head>
<body>

<header class="site-header">
  <div class="brand"><span class="brand-mark"></span><span class="brand-name">VantiQor</span></div>

  <div class="main-tab tab-order">
    <svg width="46" height="36" viewBox="0 0 46 36"><rect x="2" y="2" width="42" height="28" rx="3" fill="#b5b5b5"/><rect x="8" y="8" width="30" height="16" fill="#d9d9d9"/><rect x="14" y="31" width="18" height="4" fill="#b5b5b5"/></svg>
    Order a Test
  </div>
  <div class="main-tab tab-dashboard">
    <svg width="40" height="38" viewBox="0 0 40 38"><rect x="10" y="2" width="28" height="24" rx="2" fill="none" stroke="#84a41a" stroke-width="4"/><rect x="2" y="12" width="28" height="24" rx="2" fill="#e8e8e8" stroke="#84a41a" stroke-width="4"/></svg>
    Dashboard
  </div>

  <span class="social" style="left:1005px"></span>
  <span class="social" style="left:1066px"></span>
  <span class="social" style="left:1127px"></span>
</header>

<nav class="icon-bar">
  <div class="dash-item" style="left:86px">
    <div class="dash-icon"><svg width="56" height="50" viewBox="0 0 56 50"><rect x="3" y="3" width="50" height="34" rx="3" fill="none" stroke="#555a5c" stroke-width="5"/><polyline points="12,22 20,22 24,13 30,29 34,20 44,20" fill="none" stroke="#555a5c" stroke-width="3"/><rect x="20" y="40" width="16" height="4" fill="#555a5c"/><rect x="14" y="44" width="28" height="4" fill="#555a5c"/></svg></div>
    Confirmation
  </div>
  <div class="dash-item" style="left:258px">
    <div class="dash-icon"><svg width="50" height="56" viewBox="0 0 50 56"><rect x="20" y="4" width="10" height="28" rx="2" transform="rotate(25 25 18)" fill="#555a5c"/><path d="M10 40 Q22 24 38 30" fill="none" stroke="#555a5c" stroke-width="5"/><rect x="4" y="46" width="42" height="7" rx="2" fill="#555a5c"/><rect x="14" y="38" width="20" height="8" fill="#555a5c"/></svg></div>
    Nearest Lab
  </div>
  <div class="dash-item" style="left:432px">
    <div class="dash-icon"><svg width="44" height="56" viewBox="0 0 44 56"><rect x="3" y="6" width="38" height="47" rx="4" fill="none" stroke="#555a5c" stroke-width="4"/><rect x="13" y="2" width="18" height="8" rx="2" fill="#555a5c"/><g fill="#555a5c"><rect x="10" y="18" width="5" height="5"/><rect x="18" y="19" width="17" height="3"/><rect x="10" y="28" width="5" height="5"/><rect x="18" y="29" width="17" height="3"/><rect x="10" y="38" width="5" height="5"/><rect x="18" y="39" width="17" height="3"/></g></svg></div>
    Receipt
  </div>
  <div class="dash-item" style="left:598px">
    <div class="dash-icon"><svg width="34" height="58" viewBox="0 0 34 58"><path d="M6 2 C6 20 28 20 28 29 C28 38 6 38 6 56" fill="none" stroke="#555a5c" stroke-width="5"/><path d="M28 2 C28 20 6 20 6 29 C6 38 28 38 28 56" fill="none" stroke="#555a5c" stroke-width="5"/><g stroke="#555a5c" stroke-width="3"><line x1="9" y1="8" x2="25" y2="8"/><line x1="12" y1="14" x2="22" y2="14"/><line x1="12" y1="44" x2="22" y2="44"/><line x1="9" y1="50" x2="25" y2="50"/></g></svg></div>
    Orders
  </div>
  <div class="dash-item is-active" style="left:768px">
    <div class="dash-icon"><div class="person-slot" role="img" aria-label="Account holder figure with stethoscope" style="background:var(--active)"></div></div>
    Account
  </div>
  <div class="dash-item" style="left:946px">
    <div class="dash-icon"><svg width="58" height="40" viewBox="0 0 58 40"><rect x="2" y="2" width="54" height="36" fill="#555a5c"/><polyline points="2,2 29,24 56,2" fill="none" stroke="#dcdcdc" stroke-width="3"/></svg><span class="badge">2</span></div>
    Inbox
  </div>
  <div class="dash-item" style="left:1115px">
    <div class="dash-icon"><div class="person-slot" role="img" aria-label="Customer service agent with headset" style="background:var(--icon)"></div></div>
    Customer<br>Service
  </div>
</nav>

<main class="panel">
  <section class="card">
    <h1 class="card-title">My Account</h1>
    <div class="field" style="left:43px;top:126px;width:466px">First Name</div>
    <div class="field" style="left:528px;top:126px;width:467px">Last Name</div>
    <div class="field" style="left:40px;top:224px;width:957px">myemail@mailvista.net</div>
    <div class="field" style="left:40px;top:320px;width:957px">18 Alder Lane, Brookfield.</div>
    <div class="field select" style="left:40px;top:417px;width:225px">December<svg width="26" height="22" viewBox="0 0 26 22"><polygon points="0,0 26,0 13,22" fill="#555a5c"/></svg></div>
    <div class="field select" style="left:280px;top:417px;width:128px">08<svg width="26" height="22" viewBox="0 0 26 22"><polygon points="0,0 26,0 13,22" fill="#555a5c"/></svg></div>
    <div class="field select" style="left:422px;top:417px;width:144px">2013<svg width="26" height="22" viewBox="0 0 26 22"><polygon points="0,0 26,0 13,22" fill="#555a5c"/></svg></div>
    <div class="submit"><span class="submit-icon"><svg width="20" height="18" viewBox="0 0 20 18"><line x1="2" y1="9" x2="17" y2="9" stroke="#fff" stroke-width="3"/><polyline points="10,2 17,9 10,16" fill="none" stroke="#fff" stroke-width="3"/></svg></span>Submit Changes</div>
  </section>
</main>

</body>
</html>
```